Need Flyer for Our Real estate Agency

Need to run General Campaign for our agency with Start of New Year as our theme ..Must have an agent's picture on the DL..
Address:
27 / 486Brindle rd, Marsden VIC 3047
Ph:03 9412 7306
email:info@kovalinrealestate.com.au
www.kovalinrealestate.com.au
Something like as attached picture..
Target Market(s)
Home Buyers
Industry/Entity Type
Real Estate Agent
Requirements
Must have
- Our Logo Colours

```html
<!DOCTYPE html>
<html lang="en">
<head>
<meta charset="utf-8">
<title>Kovalin Real Estate – DL Flyer</title>
<link rel="stylesheet" href="https://fonts.googleapis.com/css2?family=Lato:wght@400;700;900&display=swap">
<style>
  :root {
    --navy: #1e2452;
    --navy-deep: #171c44;
    --cream: #eeeee2;
    --page: #e6e3dc;
    --sky-top: #4fa3d6;
    --sky-low: #8bbad0;
    --house-warm: #b08a5c;
    --pool: #2e4f5a;
    --portrait: #c9cbc4;
  }
  * { margin: 0; padding: 0; box-sizing: border-box; }
  html, body {
    width: 1200px;
    height: 858px;
    overflow: hidden;
    background: var(--page);
  }
  .canvas {
    position: relative;
    width: 1200px;
    height: 858px;
    display: flex;
    align-items: center;
    justify-content: center;
  }
  .dl-flyer {
    width: 368px;
    height: 780px;
    display: block;
    box-shadow: 0 6px 24px rgba(0,0,0,0.18);
    font-family: 'Lato', sans-serif;
  }
  .brand-name { font-size: 44px; font-weight: 400; letter-spacing: 5px; fill: var(--cream); }
  .brand-sub { font-size: 10px; font-weight: 400; letter-spacing: 3px; fill: var(--cream); }
  .agent-name { font-size: 23px; font-weight: 700; fill: var(--cream); }
  .agent-role { font-size: 9.5px; font-weight: 700; letter-spacing: 0.5px; fill: var(--cream); }
  .phone { font-size: 24px; font-weight: 900; fill: var(--navy); }
  .address { font-size: 14px; font-weight: 700; fill: var(--navy); }
  .web-line { font-size: 14px; font-weight: 700; fill: var(--cream); }
</style>
</head>
<body>
<main class="canvas">
  <svg class="dl-flyer" viewBox="0 0 368 780" xmlns="http://www.w3.org/2000/svg">
    <defs>
      <linearGradient id="propertyTones" x1="0" y1="0" x2="0" y2="1">
        <stop offset="0" stop-color="var(--sky-top)"/>
        <stop offset="0.35" stop-color="var(--sky-low)"/>
        <stop offset="0.6" stop-color="var(--house-warm)"/>
        <stop offset="1" stop-color="var(--pool)"/>
      </linearGradient>
    </defs>

    <!-- background -->
    <rect class="flyer-base" width="368" height="780" fill="var(--navy)"/>

    <!-- brand -->
    <text class="brand-name" x="184" y="150" text-anchor="middle">KOVALIN</text>
    <text class="brand-sub" x="184" y="172" text-anchor="middle">REAL ESTATE</text>

    <!-- property photo area -->
    <path class="property-photo" role="img" aria-label="Photo of a lit luxury home at dusk with a reflecting pool"
          d="M0,205 Q255,255 368,585 L368,780 L0,780 Z" fill="url(#propertyTones)"/>
    <path class="photo-edge" d="M0,195 Q262,245 368,572" fill="none" stroke="var(--cream)" stroke-width="4"/>

    <!-- contact panel -->
    <path class="contact-panel" d="M0,780 L0,660 Q20,575 120,560 L368,560 L368,780 Z" fill="var(--cream)"/>

    <!-- agent portrait -->
    <circle class="portrait-ring" cx="290" cy="540" r="82" fill="var(--navy)"/>
    <circle class="agent-portrait" role="img" aria-label="Agent portrait" cx="290" cy="540" r="74" fill="var(--portrait)"/>

    <!-- name pill -->
    <path class="name-pill" d="M74,555 L250,555 L250,610 L74,610 Q46,610 46,582 Q46,555 74,555 Z" fill="var(--navy)"/>
    <text class="agent-name" x="148" y="584" text-anchor="middle">NAME HERE</text>
    <text class="agent-role" x="148" y="600" text-anchor="middle">MARKETING MANAGER</text>

    <!-- contact -->
    <text class="phone" x="184" y="648" text-anchor="middle">Ph:03 9412 7306</text>
    <text class="address" x="184" y="672" text-anchor="middle">27 / 486Brindle rd, Marsden VIC 3047</text>

    <!-- footer band -->
    <rect class="footer-band" x="0" y="692" width="368" height="88" fill="var(--navy)"/>
    <text class="web-line" x="184" y="728" text-anchor="middle">email:info@kovalinrealestate.com.au</text>
    <text class="web-line" x="184" y="750" text-anchor="middle">www.kovalinrealestate.com.au</text>
  </svg>
</main>
</body>
</html>
```